Commercial Real Estate Property Sign

Design a 4' x 4' sign that pops. Refer to examples.

Must include the following information:
A space to list (For Sale, For Lease, Build-to-Suite or Available)
BrightKeel,LLC
Commercial Real Estate
company website
My Name (Marcus Pellow)
My Phone #

Industry/Entity Type

Real Estate

```html
<!DOCTYPE html>
<html lang="en">
<head>
<meta charset="utf-8">
<title>BrightKeel LLC – For Lease Sign</title>
<link href="https://fonts.googleapis.com/css2?family=Barlow:wght@400;500;700;800&display=swap" rel="stylesheet">
<style>
  :root {
    --orange: #e8670a;
    --charcoal: #3b3b3c;
    --ink: #1f1c1b;
    --white: #ffffff;
    --black: #000000;
  }
  * { margin: 0; padding: 0; box-sizing: border-box; }
  html, body { width: 1200px; height: 1200px; overflow: hidden; }
  body { font-family: "Barlow", Arial, sans-serif; background: var(--orange); }

  .sign { position: relative; width: 1200px; height: 1200px; background: var(--orange); }

  .brand-band {
    position: absolute; top: 0; left: 0; width: 1200px; height: 275px;
    background: var(--charcoal);
  }
  .brand-name {
    position: absolute; top: 56px; left: 0; width: 1200px;
    text-align: center;
    color: var(--white); font-weight: 500; font-size: 96px;
    letter-spacing: 1px; line-height: 1;
  }
  .brand-tagline {
    position: absolute; top: 176px; left: 0; width: 1200px;
    display: flex; align-items: center; justify-content: center; gap: 22px;
  }
  .brand-tagline .rule { width: 268px; height: 3px; background: var(--orange); }
  .brand-tagline span {
    color: var(--white); font-size: 44px; font-weight: 500; letter-spacing: 1px;
  }

  .listing-status {
    position: absolute; top: 442px; left: 0; width: 1200px;
    display: flex; align-items: center; justify-content: center; gap: 22px;
    font-weight: 800; font-size: 88px;
  }
  .listing-lead { color: var(--white); }
  .listing-lead .dark { color: var(--ink); }
  .listing-type {
    background: var(--black); color: var(--white);
    height: 113px; padding: 0 20px;
    display: flex; align-items: center; letter-spacing: 2px;
  }

  .agent-name {
    position: absolute; top: 712px; width: 1200px; text-align: center;
    color: var(--ink); font-size: 96px; font-weight: 400; letter-spacing: 2px;
  }
  .agent-phone {
    position: absolute; top: 825px; width: 1200px; text-align: center;
    color: var(--ink); font-size: 134px; font-weight: 800; letter-spacing: 3px;
    line-height: 1.1;
  }
  .website {
    position: absolute; top: 1062px; width: 1200px;
    display: flex; align-items: center; justify-content: center; gap: 24px;
    color: var(--ink); font-size: 74px; font-weight: 800;
  }
  .website svg { width: 58px; height: 58px; }
</style>
</head>
<body>
  <div class="sign">
    <header class="brand-band">
      <div class="brand-name">BrightKeel LLC</div>
      <div class="brand-tagline">
        <div class="rule"></div>
        <span>Commercial Real Estate</span>
        <div class="rule"></div>
      </div>
    </header>

    <div class="listing-status">
      <span class="listing-lead"><span class="dark">For</span> Space</span>
      <span class="listing-type">FOR LEASE</span>
    </div>

    <div class="agent-name">Marcus Pellow</div>
    <div class="agent-phone">469.555.0172</div>

    <div class="website">
      <svg viewBox="0 0 40 40" fill="none" stroke="#1f1c1b" stroke-width="3" aria-hidden="true">
        <circle cx="20" cy="20" r="17"/>
        <ellipse cx="20" cy="20" rx="8" ry="17"/>
        <line x1="3" y1="20" x2="37" y2="20"/>
        <line x1="6" y1="11" x2="34" y2="11"/>
        <line x1="6" y1="29" x2="34" y2="29"/>
      </svg>
      <span>www.MyBrightKeel.com</span>
    </div>
  </div>
</body>
</html>
```